Business Cards Design for the electrical wholesaler: clean bold dynamic :)

We need a business card design that would follow our latest brand guidelines. As an electrical wholesaler we want to bring a fresh look and feel into the industry. The design should be clean bold and dynamic. It should come alive with the renewed energy of our green colour. Our grey colour should keep things balanced and complement the notion of maturity and responsibility. We employ Lato as a corporate font however are not bound by this font and we’re open to interpretation here.

Target Market(s)

Electrical contractors

Industry/Entity Type

Business

Contact Information for Business Card

Logo
Name & Surname: Halyna Dorosh
Job Title: Director of Marketing
Email: halya.dorosh@quillmail.example
Cell phone: XXX.XXX.XXXX
Address: 20517 - 87 Ave. Edmonton, AB, Canada. T6K 4N8
Business Phone: 780.555.0184
Website: www.brovix.example

Font styles to use
Other font styles liked:
• Lato

Requirements
Must have
• Logo & website
Nice to have
• Brand elements - some of them you may find in the attached Brand Guidelines (e.g. three lines on the background signifying "W")

```html
<!DOCTYPE html>
<html lang="en">
<head>
<meta charset="utf-8">
<title>Brovix Business Card</title>
<link rel="stylesheet" href="https://fonts.googleapis.com/css2?family=Work+Sans:wght@400;500;600&display=swap">
<style>
  :root {
    --brand-green: #8cc63f;
    --brand-grey: #4d4d4f;
    --text-grey: #3c3c3e;
    --card-white: #ffffff;
    --card-dark-top: #1e1e1f;
    --card-dark-bottom: #2c2c2d;
    --backdrop: #161617;
    --mark-light: #bdbdbd;
  }
  * { margin: 0; padding: 0; box-sizing: border-box; }
  html, body {
    width: 1200px; height: 897px; overflow: hidden;
    background: var(--backdrop);
    font-family: "Work Sans", sans-serif;
  }
  .canvas { position: relative; width: 1200px; height: 897px; }
  .card {
    position: absolute; left: 303px; width: 595px; height: 338px;
    border-radius: 22px; overflow: hidden;
  }
  .card--front { top: 92px; background: var(--card-white); color: var(--text-grey); }
  .card--back {
    top: 469px;
    background: radial-gradient(ellipse at 70% 60%, var(--card-dark-bottom), var(--card-dark-top) 70%);
  }
  .brand-name {
    position: absolute; left: 33px; top: 26px;
    font-size: 44px; font-weight: 500; color: var(--brand-grey);
    letter-spacing: -0.5px; line-height: 1;
  }
  .holder { position: absolute; right: 34px; top: 38px; text-align: right; }
  .holder__name { font-size: 23px; font-weight: 500; color: var(--brand-green); line-height: 1.1; }
  .holder__role { font-size: 15px; color: var(--text-grey); letter-spacing: 0.5px; margin-top: 3px; }
  .contacts { position: absolute; left: 33px; top: 204px; list-style: none; font-size: 15px; letter-spacing: 0.4px; }
  .contacts li { display: flex; align-items: center; height: 19px; }
  .contacts svg { width: 10px; height: 10px; margin-right: 11px; }
  .accent { color: var(--brand-green); }
  .address { position: absolute; left: 33px; top: 276px; font-size: 15px; line-height: 20px; letter-spacing: 0.4px; }
  .brand-feature {
    position: absolute; right: 34px; bottom: 26px;
    font-size: 92px; font-weight: 600; color: var(--brand-green);
    line-height: 1; letter-spacing: -2px;
  }
  .brand-center {
    position: absolute; left: 0; right: 0; top: 120px; text-align: center;
    font-size: 76px; font-weight: 500; color: var(--mark-light);
    line-height: 1; letter-spacing: -1px;
  }
</style>
</head>
<body>
<main class="canvas">
  <section class="card card--front">
    <div class="brand-name">brovix</div>
    <div class="holder">
      <div class="holder__name">Halyna Dorosh</div>
      <div class="holder__role">Founder</div>
    </div>
    <ul class="contacts">
      <li>
        <svg viewBox="0 0 10 10" aria-hidden="true"><path d="M2 1 L4 1 L4.6 3 L3.4 4 Q4.5 6.2 6 6.6 L7 5.4 L9 6 L9 8 Q5 9 2.2 5 Q1 3 2 1 Z" fill="var(--brand-green)"/></svg>
        780.555.0184
      </li>
      <li>
        <svg viewBox="0 0 10 10" aria-hidden="true"><rect x="1" y="2.5" width="8" height="5.5" fill="none" stroke="var(--brand-green)" stroke-width="1.2"/><path d="M1 2.5 L5 5.6 L9 2.5" fill="none" stroke="var(--brand-green)" stroke-width="1.2"/></svg>
        hello@brovix.example
      </li>
      <li>
        <svg viewBox="0 0 10 10" aria-hidden="true"><g fill="none" stroke="var(--brand-green)" stroke-width="0.9"><circle cx="5" cy="5" r="4"/><ellipse cx="5" cy="5" rx="1.8" ry="4"/><path d="M1 5 H9 M1.6 3 H8.4 M1.6 7 H8.4"/></g></svg>
        www.<span class="accent">brovix</span>.example
      </li>
    </ul>
    <address class="address" style="font-style:normal">
      20517 87ave<br>
      T6K4N8 Edmonton, Alberta
    </address>
    <div class="brand-feature">brovix</div>
  </section>

  <section class="card card--back">
    <div class="brand-center">brovix</div>
  </section>
</main>
</body>
</html>
```